Maplecrest Disability - Social Security Disability Attorneys

Our company is expanding to attract clients nationwide for our social security disability practice. We have a logo, but I am looking for a creative and elegant letterhead that projects an image of being technologically advanced but still professional enough for the legal field. I am looking for the "wow factor" combined with this is still professional enough for a law practice.

Requesting letterhead and business card design
Updates

Had to update and change the logo. The previous logo had a typo. Please send updates with the new logo for consideration. The letterhead and business cards should be professional enough to be used for a law firm. Thanks.

Industry/Entity Type

Law Practice, Law Firm, Healthcare Industry, Government

Colors

Designer to choose colors to be used in the design.

Requirements
Nice to have
• **Please create a vertical design for the business card**

```html
<!DOCTYPE html>
<html lang="en">
<head>
<meta charset="utf-8">
<title>Maplecrest Disability – Letterhead</title>
<link href="https://fonts.googleapis.com/css2?family=Tinos:wght@400;700&family=Lato:wght@400;700&display=swap" rel="stylesheet">
<style>
  :root {
    --backdrop: #e9eaee;
    --paper: #ffffff;
    --brand-blue: #27408f;
    --ink: #1c1c1c;
    --signature-tone: #d9ddef;
    --rule: #8a8a8a;
    --muted: #333333;
  }
  * { box-sizing: border-box; margin: 0; padding: 0; }
  html, body {
    width: 1200px; height: 900px; overflow: hidden;
    background: var(--backdrop);
  }
  .canvas {
    width: 1200px; height: 900px;
    display: flex; align-items: center; justify-content: center;
  }
  .letterhead {
    position: relative;
    width: 664px; height: 860px;
    background: var(--paper);
    box-shadow: 0 2px 10px rgba(0,0,0,.12);
    font-family: "Tinos", "Times New Roman", serif;
    color: var(--ink);
    padding: 0 78px;
  }
  .brand {
    display: flex;
    align-items: center;
    gap: 10px;
    padding-top: 78px;
    height: 130px;
  }
  .brand-mark {
    width: 12px; height: 12px;
    border-radius: 50%;
    background: var(--brand-blue);
    flex: none;
  }
  .brand-name {
    font-size: 20px;
    font-weight: 400;
    color: var(--ink);
  }
  .recipient {
    display: flex;
    margin-top: 40px;
    font-size: 12.5px;
    line-height: 15px;
  }
  .recipient-label { width: 40px; }
  .recipient address { font-style: normal; }
  .salutation { margin-top: 30px; font-size: 12.5px; }
  .body-copy {
    margin-top: 18px;
    font-size: 12.3px;
    line-height: 15.5px;
  }
  .body-copy p + p { margin-top: 16px; }
  .closing { margin-top: 18px; font-size: 12.5px; }
  .signature {
    display: block;
    width: 180px; height: 40px;
    margin-top: 6px;
    background: var(--signature-tone);
    border-radius: 3px;
  }
  .contact {
    position: absolute;
    left: 92px; bottom: 0;
    height: 110px;
    border-left: 1px solid var(--rule);
    padding: 10px 0 0 12px;
    font-family: "Lato", Arial, sans-serif;
    font-size: 8.5px;
    line-height: 15px;
    color: var(--muted);
    text-transform: uppercase;
  }
  .contact b { font-weight: 700; }
</style>
</head>
<body>
<main class="canvas">
  <article class="letterhead">
    <header class="brand">
      <span class="brand-mark"></span>
      <div class="brand-name">Maplecrest Disability</div>
    </header>

    <section class="recipient">
      <div class="recipient-label">To:</div>
      <address>
        Mr./Mrs. Customerand Partner<br>
        220 Harbor Street<br>
        New York<br>
        NY 10014
      </address>
    </section>

    <p class="salutation">Dear Customer,</p>

    <section class="body-copy">
      <p>Lorem ipsum dolor sit amet, consetetur sadipscing elitr, sed diam nonumy eirmod tempor invidunt ut labore et dolore magna aliquyam erat, sed diam voluptua. At vero eos et accusam et justo duo dolores et ea rebum. Stet clita kasd gubergren, no sea takimata sanctus est Lorem ipsum dolor sit amet. Lorem ipsum dolor sit amet, consetetur sadipscing elitr, sed diam nonumy eirmod tempor invidunt ut labore et dolore magna aliquyam erat, sed diam voluptua. At vero eos et accusam et justo duo dolores et ea rebum. Stet clita kasd gubergren, no sea takimata sanctus est Lorem ipsum dolor sit amet. Lorem ipsum dolor sit amet, consetetur sadipscing elitr, sed diam nonumy eirmod tempor invidunt ut labore et dolore magna aliquyam erat, sed diam voluptua. At vero eos et accusam et justo duo dolores et ea rebum. Stet clita kasd gubergren, no sea takimata sanctus est Lorem ipsum dolor sit amet.</p>
      <p>Duis autem vel eum iriure dolor in hendrerit in vulputate velit esse molestie consequat, vel illum dolore eu feugiat nulla facilisis at vero eros et accumsan et iusto odio dignissim qui blandit praesent luptatum zzril delenit augue duis dolore te feugait nulla facilisi. Lorem ipsum dolor sit amet, consectetuer adipiscing elit, sed diam nonummy nibh euismod tincidunt ut laoreet dolore magna aliquam erat volutpat.</p>
      <p>Nam liber tempor cum soluta nobis eleifend option congue nihil imperdiet doming id quod mazim placerat facer possim assum. Lorem ipsum dolor sit amet, consectetuer adipiscing elit, sed diam nonummy nibh euismod tincidunt ut laoreet dolore magna aliquam erat volutpat. Ut wisi enim ad minim veniam, quis nostrud exerci tation ullamcorper suscipit lobortis nisl ut aliquip ex ea commodo consequat.</p>
    </section>

    <p class="closing">Sincerely,</p>
    <span class="signature" role="img" aria-label="Handwritten signature of Daniel Whitford"></span>

    <footer class="contact">
      1840 Ridgeview Court<br>
      Brookhaven, GA 30319<br>
      <b>P:</b> 404-555-0142<br>
      <b>F:</b> 404-555-0187
    </footer>
  </article>
</main>
</body>
</html>
```